Web Design Project

Design of a complete website that has a quality and professional feel that offers video training. I have uploaded some ideas on how I am visualising the site should operate and hor the pages should interconnect. What I am NOT is a web designer, this is why I am looking for someone with the smarts and vision to make this happen, so I need someone who would like to take on this project and deliver ideas and suggestions to make this work on an automated basis. I am visualising that each page posted should be able to be edited from a back office with images, text, hyperlinks to video views and to document downloads.

Once completed and operational there would be a need for fixes, changes and adjustments as needed though I would envisage basic content would be supplied by me through the back office.

If you dont think that this project can be done within this budget, then please explain to me why and what you believe it is worth to complete. I am happy to consider all options and ideas.
Updates

Project Deadline Extended
Reason: I posted two competitions here on sketch forge at the same time, logo design and web design. This has delayed my involvement with the web design project as I needed to first settle on a logo design which has now been completed. I have not had a great deal of time available to review submitted designs and of those that have been submitted to date I am not entirely happy with. I will over the next 14 days focus on the web design element. I am wanting a complete website produced and maintained with the design being the first stage. When submitting designs, please provide an indication of if you are interested in going on to produce the complete website and your cost to do this. If you require additional information I can be contacted on tim@brightlanecoaching.com.au I will be reviewing the submitted designs so far and providing feedback on these and look forward to seeing new ideas. Tim

Target Market(s)

Mostly women with some men, probably a mix of 90/10

Industry/Entity Type

Training

Requirements
Must have
• Fast loading, user friendly, payment option my via coin vault account, the site will have a logo (currently being designed on forge), a customer database that is added to as people take up membership/purchase, needs to have auto reminders of expiring memberships and ability to create e-newsletters with their own hyperlinks to pages and tracking of read items if possible. Back office that can add delete and edit all pages adding links, photos etc.
If you have ideas please express them, I am happy to discuss any issues. I have uploaded an outline of how I am thinking this should be but I am happy to discuss your ideas.

The site needs to operate automatically with subscriptions/memberships payments provision of access to paid for elements

This project needs to be completed in a timely manner.
Nice to have
• ** Auto payment through coin vault
** auto registration and access generation
** auto reminders when membership period expires
** Ability to choose what video training is included within the membetship period
** HTML newsletters with tracking
Should not have
• The site should not look unprofessional and unappealing or take a long time to load pages, I am open to colour scheme ideas.

```html
<!DOCTYPE html>
<html lang="en">
<head>
<meta charset="utf-8">
<title>Video Training Center</title>
<link href="https://fonts.googleapis.com/css2?family=Raleway:wght@200;400&family=Open+Sans:wght@400;600;700&family=Roboto+Condensed:wght@400;700&family=Bitter:wght@400&family=Arimo:wght@400;700&display=swap" rel="stylesheet">
<style>
:root{
  --blue:#12b2ea;
  --blue-dark:#0a94c6;
  --nav-btn:#0b9fd2;
  --ink:#222;
  --text:#555;
  --muted:#777;
  --panel-border:#a8a8a8;
  --card:#e4e4e4;
  --card-bar:#d2d2d2;
  --band:#f1f1f1;
  --tab:#cfcfcf;
  --tab-text:#6d6d6d;
  --dark-btn:#333;
  --white:#fff;
}
*{box-sizing:border-box;margin:0;padding:0}
html,body{width:978px;height:1200px;overflow:hidden}
body{background:var(--band);font-family:"Arimo",Arial,sans-serif;color:var(--text);position:relative}
.site-header{position:absolute;left:0;top:0;width:978px;height:78px;background:var(--blue)}
.brand{position:absolute;left:48px;top:22px;display:flex;align-items:center;gap:9px;color:var(--white);font-family:"Open Sans",sans-serif;font-weight:700;font-size:25px;letter-spacing:.2px}
.brand-mark{width:14px;height:14px;border-radius:50%;background:var(--white)}
.main-nav{position:absolute;left:403px;top:25px;display:flex;gap:5px}
.main-nav a{display:block;height:28px;line-height:28px;padding:0 9px;background:var(--nav-btn);color:var(--white);font-family:"Roboto Condensed",sans-serif;font-size:14px;text-decoration:none}
.main-nav a.current{background:var(--white);color:var(--blue);position:relative}
.main-nav a.current::after{content:"";position:absolute;left:50%;bottom:-5px;margin-left:-5px;border:5px solid transparent;border-bottom:0;border-top-color:var(--white)}
.login{position:absolute;left:870px;top:23px;height:32px;line-height:30px;padding:0 10px;background:#2c2c2c;border:1px solid #555;border-radius:3px;color:var(--white);font-family:"Roboto Condensed",sans-serif;font-size:15px;text-decoration:none}
.top-zone{position:absolute;left:0;top:78px;width:978px;height:590px;background:linear-gradient(#fff,#f7f7f7 80%,#ececec)}
.hero-panel{position:absolute;left:48px;top:88px;width:882px;height:503px;background:var(--white);border:4px solid var(--panel-border);border-bottom:0}
.hero-title{position:absolute;left:75px;top:110px;font-family:"Raleway",sans-serif;font-weight:200;font-size:50px;line-height:45px;color:var(--blue)}
.hero-lead{position:absolute;left:76px;top:232px;width:380px;font-family:"Open Sans",sans-serif;font-weight:700;font-size:16px;line-height:21px;color:var(--ink)}
.hero-points{position:absolute;left:78px;top:286px;list-style:none;font-size:13px;line-height:23px;color:#666}
.hero-points li{padding-left:17px;position:relative}
.hero-points li::before{content:"";position:absolute;left:1px;top:7px;width:8px;height:4px;border-left:2px solid var(--blue);border-bottom:2px solid var(--blue);transform:rotate(-45deg)}
.hero-points b{color:var(--ink)}
.hero-video{position:absolute;left:495px;top:115px;width:409px;height:238px;border:5px solid #8d8d8d;border-radius:3px;background:linear-gradient(#f4f4f4,#dcdad4 60%,#c9c4ba)}
.play{position:absolute;left:50%;top:50%;width:80px;height:80px;margin:-45px 0 0 -40px;border-radius:50%;background:rgba(60,60,60,.8)}
.play::after{content:"";position:absolute;left:32px;top:24px;border-left:26px solid #fff;border-top:16px solid transparent;border-bottom:16px solid transparent}
.hero-actions{position:absolute;left:495px;top:363px;display:flex;gap:9px}
.btn{height:33px;line-height:33px;font-family:"Bitter",serif;font-size:17px;color:var(--white);border-radius:2px;padding:0 12px}
.btn-primary{width:196px;background:linear-gradient(var(--blue),var(--blue-dark));display:flex;align-items:center;justify-content:space-between}
.btn-primary i{width:20px;height:20px;border-radius:50%;background:#0a7fae;position:relative}
.btn-primary i::after{content:"";position:absolute;left:8px;top:5px;border-left:6px solid var(--white);border-top:5px solid transparent;border-bottom:5px solid transparent}
.btn-dark{width:205px;background:var(--dark-btn);text-align:center}
.video-row{position:absolute;left:76px;top:409px;display:flex;gap:16px}
.video-thumb{position:relative;width:195px;height:151px;border:3px solid #777;border-radius:3px;overflow:hidden}
.video-thumb .shot{position:absolute;inset:0}
.shot-person{background:linear-gradient(#e8e8e8,#9a9a9a)}
.shot-screen{background:linear-gradient(90deg,#f3f5f8 0 45%,#fbfbfb 45%)}
.video-thumb .mini-play{position:absolute;left:50%;top:56px;width:40px;height:40px;margin-left:-20px;border-radius:50%;background:rgba(70,70,70,.8)}
.video-thumb .mini-play::after{content:"";position:absolute;left:16px;top:12px;border-left:12px solid #fff;border-top:8px solid transparent;border-bottom:8px solid transparent}
.video-thumb .caption{position:absolute;left:0;right:0;bottom:0;height:33px;line-height:33px;background:rgba(40,40,40,.72);color:var(--white);text-align:center;font-family:"Open Sans",sans-serif;font-weight:700;font-size:14.5px}
.tab-bar{position:absolute;left:48px;top:591px;width:882px;height:59px;display:flex;background:var(--tab)}
.tab{flex:1;line-height:59px;text-align:center;font-family:"Roboto Condensed",sans-serif;font-weight:700;font-size:21px;color:var(--tab-text);border-left:1px solid #e2e2e2}
.tab.active{flex:0 0 295px;background:var(--blue);color:var(--white);position:relative;border:0}
.tab.active::before{content:"";position:absolute;left:138px;top:-12px;border:12px solid transparent;border-top:0;border-bottom-color:var(--blue)}
.feature-grid{position:absolute;left:48px;top:681px;width:882px;display:grid;grid-template-columns:repeat(3,285px);column-gap:13.5px;row-gap:14px}
.feature{position:relative;height:115px;background:var(--card)}
.feature-icon{position:absolute;left:11px;top:11px;width:63px;height:63px;background:var(--white);border-radius:3px;display:flex;align-items:center;justify-content:center}
.feature-icon::after{content:"";position:absolute;left:50%;bottom:-7px;margin-left:-7px;border:7px solid transparent;border-bottom:0;border-top-color:var(--white)}
.feature h3{position:absolute;left:85px;top:14px;font-size:13px;font-weight:700;color:#555;letter-spacing:.2px}
.feature p{position:absolute;left:85px;top:33px;width:185px;font-size:10px;line-height:12px;color:#8a8a8a;letter-spacing:.3px}
.feature .more{position:absolute;left:0;right:0;bottom:0;height:25px;line-height:25px;background:var(--card-bar);text-align:right;padding-right:9px;font-size:10px;font-weight:700;color:#555;letter-spacing:.3px}
.section-title{position:absolute;top:933px;font-family:"Bitter",serif;font-size:20px;color:var(--blue)}
.blog{position:absolute;left:48px;top:963px;width:609px;height:186px;background:var(--white);display:flex;padding:12px 14px 0;gap:22px}
.post{flex:1;position:relative}
.post h4{font-family:"Bitter",serif;font-weight:400;font-size:13px;color:#333;margin-bottom:8px}
.post p{font-size:9.4px;line-height:14.1px;color:#777}
.post .more{position:absolute;right:0;top:156px;font-size:11px;font-weight:700;color:#333}
.support{position:absolute;left:675px;top:963px;width:255px;height:186px;background:var(--white)}
.support-links{position:absolute;left:12px;top:12px;list-style:none;font-size:11px;line-height:19.5px;color:#333}
.support-links li::before{content:"› ";color:#777}
.badge{position:absolute;right:16px;display:flex;align-items:center;gap:6px;padding:0 8px;border-radius:3px;background:var(--blue);color:var(--white);font-size:12px;font-weight:700}
.badge i{width:12px;height:12px;background:var(--white)}
.badge-chirp{top:30px;height:40px}
.badge-friend{top:135px;height:38px;background:#2b4c8c}
.support hr{position:absolute;left:0;right:0;top:94px;border:0;border-top:1px solid #e6e6e6}
.contact-lines{position:absolute;left:13px;top:103px;font-size:11px;line-height:19.5px;color:#333}
.contact-lines b{font-weight:700}
.site-footer{position:absolute;left:0;top:1162px;width:978px;height:38px;background:#dcdcdc;font-family:"Open Sans",sans-serif;font-size:10px;color:#555}
.footer-nav{position:absolute;left:48px;top:13px}
.footer-nav span{margin:0 5px;color:#888}
.copyright{position:absolute;right:48px;top:13px}
</style>
</head>
<body>
<header class="site-header">
  <div class="brand"><span class="brand-mark"></span>Video Training Center</div>
  <nav class="main-nav">
    <a class="current" href="#">Home</a><a href="#">About Us</a><a href="#">Sample Training Video</a><a href="#">Memberships</a><a href="#">Contact Us</a>
  </nav>
  <a class="login" href="#">Log In</a>
</header>

<div class="top-zone"></div>
<section class="hero-panel"></section>
<h1 class="hero-title">Lorem Ipsum is<br>simply dummy</h1>
<p class="hero-lead">Contrary to popular belief, Lorem Ipsum is not simply random text. It has roots.</p>
<ul class="hero-points">
  <li><b>Lorem ipsum:</b> dolor sit amet, consectetur adipiscing elit.</li>
  <li><b>Morbi eget:</b> erat mi. Praesent ultrices, sem vel viverra tempus,</li>
  <li><b>Nibh tortor:</b> condimentum arcu, in tempus eros est vel metus.</li>
  <li><b>Sed aliquam:</b> ultrices mauris sit amet mattis.</li>
</ul>
<div class="hero-video" role="img" aria-label="Video still of a bright empty training classroom with desks and a whiteboard"><span class="play"></span></div>
<div class="hero-actions">
  <a class="btn btn-primary">See More Features <i></i></a>
  <a class="btn btn-dark">Take The Feature Tour</a>
</div>

<div class="video-row">
  <div class="video-thumb"><div class="shot shot-person" role="img" aria-label="Video still of a presenter in an office"></div><span class="mini-play"></span><div class="caption">LedgerOne Training Video</div></div>
  <div class="video-thumb"><div class="shot shot-screen" role="img" aria-label="Screen recording of accounting software"></div><span class="mini-play"></span><div class="caption">Manual Accounting VL</div></div>
  <div class="video-thumb"><div class="shot shot-screen" role="img" aria-label="Screen recording of accounting software"></div><span class="mini-play"></span><div class="caption">Cash Accounting VL</div></div>
  <div class="video-thumb"><div class="shot shot-screen" role="img" aria-label="Screen recording of accounting software"></div><span class="mini-play"></span><div class="caption">Accrual Accounting VL</div></div>
</div>

<div class="tab-bar">
  <div class="tab active">Nulla in nisl lectus. Phasellus</div>
  <div class="tab">Maecenas consectetur nunc</div>
  <div class="tab">Proin aliquam blandit ullam</div>
</div>

<section class="feature-grid">
  <article class="feature">
    <div class="feature-icon"><svg width="36" height="30" viewBox="0 0 36 30"><path d="M1 10 18 1l17 9v19H1z" fill="#12b2ea"/><path d="M1 10l17 11 17-11" fill="none" stroke="#fff" stroke-width="2"/><path d="M9 12h18M9 16h18" stroke="#fff" stroke-width="1.6"/></svg></div>
    <h3>Lorem ipsum dolor sit amet:</h3>
    <p>Consectetur adipiscing elit. Morbi eget erat mi. Praesent ultrices, sem vel viverra tempus, nibh</p>
    <div class="more">Read more ›</div>
  </article>
  <article class="feature">
    <div class="feature-icon"><svg width="40" height="36" viewBox="0 0 40 36"><path d="M2 2v32h36" fill="none" stroke="#12b2ea" stroke-width="4"/><path d="M6 28 15 14l7 8 12-16" fill="none" stroke="#12b2ea" stroke-width="4"/></svg></div>
    <h3>Ut aliquam ullamcorper:</h3>
    <p>Nunc ac gravida massa. Praesent pellentesque egestas nulla.</p>
    <div class="more">Read more ›</div>
  </article>
  <article class="feature">
    <div class="feature-icon"><svg width="28" height="40" viewBox="0 0 28 40"><path d="M4 12a10 10 0 1 1 14 9c-3 2-4 3-4 7" fill="none" stroke="#12b2ea" stroke-width="6"/><rect x="11" y="32" width="6" height="6" fill="#12b2ea"/></svg></div>
    <h3>Nulla in nisl lectus:</h3>
    <p>Phasellus eleifend sodales urna quis hendrerit. Maecenas consectet nunc eget ante</p>
    <div class="more">Read more ›</div>
  </article>
  <article class="feature">
    <div class="feature-icon"><svg width="40" height="36" viewBox="0 0 40 36"><path d="M1 3h7l5 19h20l5-14H11" fill="none" stroke="#12b2ea" stroke-width="4"/><rect x="12" y="9" width="23" height="12" fill="#12b2ea"/><circle cx="16" cy="30" r="4" fill="#12b2ea"/><circle cx="30" cy="30" r="4" fill="#12b2ea"/></svg></div>
    <h3>Integer vel neque non eros:</h3>
    <p>Aliquam quam quam, volutpat sit amet egestas ut, malesuada eget odio.</p>
    <div class="more">Read more ›</div>
  </article>
  <article class="feature">
    <div class="feature-icon"><svg width="40" height="40" viewBox="0 0 40 40"><circle cx="20" cy="20" r="17" fill="none" stroke="#12b2ea" stroke-width="2" stroke-dasharray="4 3"/><circle cx="20" cy="20" r="9" fill="#12b2ea" opacity=".7"/></svg></div>
    <h3>Nulla at leo nibh, a interdum:</h3>
    <p>Duis eget velit sed lacus gravida vehicula. Pellentesque habitant morbi tristique senectus</p>
    <div class="more">Read more ›</div>
  </article>
  <article class="feature">
    <div class="feature-icon"><svg width="26" height="42" viewBox="0 0 26 42"><rect x="1" y="1" width="24" height="40" rx="3" fill="#12b2ea"/><rect x="4" y="6" width="18" height="27" fill="#fff"/><circle cx="13" cy="37" r="2" fill="#fff"/></svg></div>
    <h3>Vestibulum ac lectus vitae:</h3>
    <p>Donec volutpat pulvinar purus in faucibus. Etiam in nulla nisl, eget</p>
    <div class="more">Read more ›</div>
  </article>
</section>

<h2 class="section-title" style="left:48px">Blog</h2>
<h2 class="section-title" style="left:675px">Help &amp; Support</h2>

<section class="blog">
  <article class="post">
    <h4>Lorem Ipsum is simply dummy</h4>
    <p>Lorem Ipsum is simply dummy text of the printing and typesetting industry. Lorem Ipsum has been the industry's standard dummy text ever since the 1500s, when an unknown printer took a galley of type and scrambled it to make a type specimen book. It has survived not only five centuries, but also the leap was popularised in the 1960s with the release of Sheetline sheets containing Lorem Ipsum passages, and more recently with desktop publishing software like Folio PageSetter including versions of Lorem Ipsum.</p>
    <span class="more">Read more ›</span>
  </article>
  <article class="post">
    <h4>Lorem Ipsum is simply dummy</h4>
    <p>Lorem Ipsum is simply dummy text of the printing and typesetting industry. Lorem Ipsum has been the industry's standard dummy text ever since the 1500s, when an unknown printer took a galley of type and scrambled it to make a type specimen book. It has survived not only five centuries, but also the leap was popularised in the 1960s with the release of Sheetline sheets containing Lorem Ipsum passages, and more recently with desktop publishing software like Folio PageSetter including versions of Lorem Ipsum.</p>
    <span class="more">Read more ›</span>
  </article>
</section>

<aside class="support">
  <ul class="support-links">
    <li>Webinars</li><li>User Group Forum</li><li>Quick Start Guide</li><li>FAQ</li>
  </ul>
  <div class="badge badge-chirp"><i></i>Chirpline</div>
  <hr>
  <div class="contact-lines">
    <div><b>Live Chat:</b> Submit Support Ticket</div>
    <div>Email Support</div>
    <div>1-800-555-0142</div>
  </div>
  <div class="badge badge-friend"><i></i>Friendwall</div>
</aside>

<footer class="site-footer">
  <div class="footer-nav">Home<span>|</span>About Us<span>|</span>Sample Training Video<span>|</span>Memberships<span>|</span>Contact Us<span>|</span>Privacy Policy<span>|</span>Terms of Service</div>
  <div class="copyright">© 2012 Video Training Center. All Rights Reserved</div>
</footer>
</body>
</html>
```